RWT Fittings Ltd Business Cards

We need a business card with our business logo. We provide window and door installations on high-rises in west coast British Colombia, Canada.

I would like my business information and details on one side of the card, and the other side the company name with logo

Target Market(s)

General Contractors

Industry/Entity Type

Construction

Contact Information for Business Card

one side i want my company name and logo in the dark theme logo that i provided

Requirements
Must have
• Marco Peltieri, 16045518293, RWTFittings@mailbox-demo.com, 1407-5194 Linden Row Burnaby BC, V5H 2K9, Owner & Manager

```html
<!DOCTYPE html>
<html lang="en">
<head>
<meta charset="utf-8">
<title>RWT Fittings Ltd – Business Cards</title>
<link href="https://fonts.googleapis.com/css2?family=Open+Sans:wght@400;700&display=swap" rel="stylesheet">
<style>
  :root {
    --backdrop-light: #4a4a4a;
    --backdrop-dark: #141414;
    --card: #1b1b1c;
    --accent: #29a8e0;
    --steel: #9a9a9a;
    --text: #e9e9e9;
  }
  * { margin: 0; padding: 0; box-sizing: border-box; }
  html, body { width: 1200px; height: 780px; overflow: hidden; }
  body {
    background: radial-gradient(ellipse at 20% 10%, var(--backdrop-light), var(--backdrop-dark) 80%);
    font-family: "Open Sans", Arial, sans-serif;
    display: flex;
    align-items: center;
    justify-content: center;
    gap: 40px;
  }
  .card {
    position: relative;
    width: 560px;
    height: 320px;
    background: var(--card);
    overflow: hidden;
    box-shadow: 0 14px 30px rgba(0,0,0,.5);
  }
  .band {
    position: absolute;
    width: 26px;
    background: var(--accent);
  }
  .band--top { left: 34px; top: 0; height: 150px; }
  .band--bottom { right: 34px; bottom: 0; height: 150px; }

  .brand {
    display: flex;
    align-items: center;
    gap: 14px;
    color: var(--accent);
    font-weight: 700;
    text-transform: uppercase;
    white-space: nowrap;
  }
  .brand__mark { background: var(--steel); flex: none; }

  /* logo side */
  .card--front .brand {
    position: absolute;
    left: 50%; top: 50%;
    transform: translate(-50%, -50%);
    font-size: 38px;
    letter-spacing: 1px;
  }
  .card--front .brand__mark { width: 40px; height: 40px; }

  /* contact side */
  .card--back .band--bottom { height: 96px; }
  .card--back .brand {
    position: absolute;
    left: 72px; top: 140px;
    font-size: 17px;
    gap: 10px;
  }
  .card--back .brand__mark { width: 22px; height: 22px; }
  .divider {
    position: absolute;
    left: 284px; top: 70px;
    width: 1px; height: 180px;
    background: var(--accent);
  }
  .contact {
    position: absolute;
    left: 298px; top: 72px;
    color: var(--text);
    font-size: 12.5px;
    line-height: 1.5;
    white-space: nowrap;
  }
  .contact__name {
    color: var(--accent);
    font-weight: 700;
    font-size: 18px;
    text-transform: uppercase;
    line-height: 1.2;
  }
  .contact__role { margin-bottom: 6px; }
  .contact__address { margin-bottom: 6px; }
  .contact__row { display: flex; align-items: center; gap: 6px; }
  .contact__row svg { width: 11px; height: 11px; flex: none; fill: var(--accent); }
</style>
</head>
<body>

  <section class="card card--front" aria-label="Logo side">
    <div class="band band--top"></div>
    <div class="band band--bottom"></div>
    <div class="brand"><span class="brand__mark"></span>RWT Fittings Ltd</div>
  </section>

  <section class="card card--back" aria-label="Contact side">
    <div class="band band--top"></div>
    <div class="band band--bottom"></div>
    <div class="brand"><span class="brand__mark"></span>RWT Fittings Ltd</div>
    <div class="divider"></div>
    <div class="contact">
      <p class="contact__name">Marco Peltieri</p>
      <p class="contact__role">Owner &amp; Manager</p>
      <p class="contact__address">1407-5194 Linden Row<br>Burnaby BC, V5H 2K9</p>
      <p class="contact__row">
        <svg viewBox="0 0 24 24" aria-hidden="true"><path d="M6.6 10.8a15.1 15.1 0 0 0 6.6 6.6l2.2-2.2c.3-.3.7-.4 1-.2 1.1.4 2.3.6 3.6.6.6 0 1 .4 1 1V20c0 .6-.4 1-1 1A17 17 0 0 1 3 4c0-.6.4-1 1-1h3.5c.6 0 1 .4 1 1 0 1.3.2 2.5.6 3.6.1.3 0 .7-.2 1z"/></svg>
        16045518293
      </p>
      <p class="contact__row">
        <svg viewBox="0 0 24 24" aria-hidden="true"><path d="M2 5h20v14H2z M3.5 6.5 12 13l8.5-6.5" fill="none" stroke="#29a8e0" stroke-width="2"/></svg>
        RWTFittings@mailbox-demo.com
      </p>
      <p class="contact__row">
        <svg viewBox="0 0 24 24" aria-hidden="true"><circle cx="12" cy="12" r="9" fill="none" stroke="#29a8e0" stroke-width="2"/><path d="M3 12h18M12 3c3 3 3 15 0 18M12 3c-3 3-3 15 0 18" fill="none" stroke="#29a8e0" stroke-width="1.6"/></svg>
        www.rwtfittings-demo.com
      </p>
    </div>
  </section>

</body>
</html>
```